Varnik Holdings — Business Card Design Brief
Overview
Design a double-sided business card for Varnik Holdings that highlights our two service arms: Varnik Communications (telecommunications) and Varnik Energy (business energy solutions). The card should feel smart and stand out when handed to clients.

Objectives
Showcase our areas of specialty clearly.
Reflect the overall Varnik / Varnik Holdings brand while acknowledging both arms.
Explore using both logos (Communications + Energy) or one unified logo, depending on the design.

Deliverables
One double-sided business card design (front + back).

Content & Copy
Front (preferred): Logo: Varnik / Varnik Holdings
Descriptor: Business Communications | Business Energy
Back:My contact details and company details
Core products: Business Mobile • Telephony • Internet • Business Energy Solutions

Brand & Visual Direction
We have a group logo currently tailored more toward telecoms, plus a separate Varnik Energy logo.
Please explore layouts that use both logos or just one, whichever works best.
Color: I wouldn't mind seeing an option using our the Blue/Purple gradient from our website (varnik-example.co.uk), but also open to non-gradient approaches and other colours..

Overall look: Smart, modern, and distinctive.
Format & Print Specs
Double-sided business card format. (Use a standard size

Must-Haves
Front: Varnik wording or Varnik Holdings wording with atleast 1 logo also on front “Business Communications | Business Energy.”

Back: Contact + company details and core products.
A design that stands out while remaining professional.

Nice-to-Have Options
A gradient version using our site’s Blue/Purple gradient.
A non-gradient version.
A dual-logo treatment versus a single-logo treatment.

Thanks
Owen

```html
<!DOCTYPE html>
<html lang="en">
<head>
<meta charset="utf-8">
<title>Varnik Holdings Business Card</title>
<link href="https://fonts.googleapis.com/css2?family=Roboto:wght@400;500;700&display=swap" rel="stylesheet">
<style>
  :root {
    --page-bg: #ececec;
    --card-bg: #ffffff;
    --navy: #1f1d6b;
    --blue: #1a6fd8;
    --blue-deep: #1457c9;
    --sky: #2fb6e6;
    --green: #5fb82f;
    --lime: #a8cc1c;
    --grey-text: #6f6f73;
    --rule: #9a9a9e;
  }
  * { box-sizing: border-box; margin: 0; padding: 0; }
  html, body { width: 1200px; height: 900px; overflow: hidden; }
  body {
    background: var(--page-bg);
    font-family: "Roboto", Arial, sans-serif;
    position: relative;
  }
  .card {
    position: absolute;
    width: 630px;
    height: 360px;
    background: var(--card-bg);
    border-radius: 22px;
    overflow: hidden;
    box-shadow: 0 10px 28px rgba(0,0,0,0.14);
  }
  .card--contact { left: 60px; top: 70px; }
  .card--products { left: 510px; top: 470px; }
  .card__wave { position: absolute; inset: 0; width: 630px; height: 360px; }

  .brand {
    position: absolute;
    display: flex;
    align-items: center;
    gap: 12px;
  }
  .brand__mark {
    width: 46px; height: 46px;
    border-radius: 50%;
    background: var(--blue);
  }
  .card--products .brand__mark { background: var(--green); }
  .brand__name {
    font-weight: 700;
    font-size: 50px;
    letter-spacing: 1px;
    color: var(--navy);
    line-height: 1;
  }
  .card--contact .brand { left: 40px; top: 78px; }
  .card--products .brand { left: 280px; top: 96px; }

  .divider {
    position: absolute;
    left: 300px; top: 38px;
    width: 1.5px; height: 200px;
    background: var(--rule);
  }
  .contact {
    position: absolute;
    left: 322px; top: 40px;
    color: var(--grey-text);
    font-size: 15px;
    line-height: 1.3;
  }
  .contact__name {
    font-size: 22px;
    font-weight: 500;
    color: var(--blue);
    text-transform: uppercase;
    letter-spacing: 0.5px;
  }
  .contact__role { font-size: 16px; margin-bottom: 8px; }
  .contact__address { margin-bottom: 8px; }
  .contact__line { display: flex; align-items: center; gap: 7px; }
  .contact__icon { width: 13px; height: 13px; flex: none; }
  .band-text { font-family: "Roboto", Arial, sans-serif; fill: #ffffff; }
</style>
</head>
<body>

<section class="card card--contact" aria-label="Business card front">
  <svg class="card__wave" viewBox="0 0 630 360" aria-hidden="true">
    <defs>
      <linearGradient id="blueBand" x1="0" y1="0" x2="1" y2="1">
        <stop offset="0" stop-color="#1457c9"/>
        <stop offset="1" stop-color="#2fb6e6"/>
      </linearGradient>
      <linearGradient id="limeStripe" x1="0" y1="0" x2="1" y2="0">
        <stop offset="0" stop-color="#a8cc1c"/>
        <stop offset="1" stop-color="#5fb82f"/>
      </linearGradient>
    </defs>
    <path d="M0,172 C160,166 270,236 350,300 C390,334 440,360 500,360 L462,360 C412,360 372,338 334,306 C256,244 160,180 0,184 Z" fill="url(#limeStripe)"/>
    <path d="M0,190 C160,185 260,250 340,310 C380,340 430,360 480,360 L0,360 Z" fill="url(#blueBand)"/>
    <text class="band-text" x="0" y="0" font-size="14" transform="translate(22 246) rotate(10)">Business Communications | Business Energy</text>
  </svg>

  <div class="brand">
    <span class="brand__name">VARNIK</span>
    <span class="brand__mark"></span>
  </div>

  <div class="divider"></div>

  <div class="contact">
    <p class="contact__name">Daniel Reyes</p>
    <p class="contact__role">Managing Director</p>
    <p class="contact__address">Your Address, City<br>State, Zip 0000</p>
    <p class="contact__line">
      <svg class="contact__icon" viewBox="0 0 16 16" aria-hidden="true"><path d="M3 1.5l3 .5 1 3.5-2 1.2a8 8 0 0 0 4.3 4.3l1.2-2 3.5 1 .5 3-2 1.5C6.5 14.5 1.5 9.5 1.5 3.5z" fill="#1a6fd8"/></svg>
      020 7946 0321
    </p>
    <p class="contact__line">
      <svg class="contact__icon" viewBox="0 0 16 16" aria-hidden="true"><rect x="1" y="3" width="14" height="10" rx="1.5" fill="#1a6fd8"/><path d="M1.5 4l6.5 5 6.5-5" stroke="#fff" stroke-width="1.3" fill="none"/></svg>
      hello@varnik-example.co.uk
    </p>
    <p class="contact__line">
      <svg class="contact__icon" viewBox="0 0 16 16" aria-hidden="true"><circle cx="8" cy="8" r="7" fill="#1a6fd8"/><path d="M1 8h14M8 1c-3 3.5-3 10.5 0 14M8 1c3 3.5 3 10.5 0 14" stroke="#fff" stroke-width="1" fill="none"/></svg>
      www.varnik-example.co.uk
    </p>
  </div>
</section>

<section class="card card--products" aria-label="Business card back">
  <svg class="card__wave" viewBox="0 0 630 360" aria-hidden="true">
    <defs>
      <linearGradient id="greenBand" x1="0" y1="0" x2="1" y2="0">
        <stop offset="0" stop-color="#9cc81e"/>
        <stop offset="1" stop-color="#4fb43a"/>
      </linearGradient>
      <linearGradient id="blueStripe" x1="0" y1="0" x2="1" y2="0">
        <stop offset="0" stop-color="#1457c9"/>
        <stop offset="1" stop-color="#2fb6e6"/>
      </linearGradient>
    </defs>
    <path d="M0,194 C200,198 340,282 630,286 L630,298 C340,298 200,214 0,210 Z" fill="url(#blueStripe)"/>
    <path d="M0,210 C200,215 340,300 630,300 L630,360 L0,360 Z" fill="url(#greenBand)"/>
    <text class="band-text" x="0" y="0" font-size="14" transform="translate(26 248) rotate(8.5)">• Business Mobile  •  Telephony  •  Internet  •  Business Energy Solutions</text>
  </svg>

  <div class="brand">
    <span class="brand__name">VARNIK</span>
    <span class="brand__mark"></span>
  </div>
</section>

</body>
</html>
```